Im open to ideas.. I was thinking on my business cards aswell as my logo. a place for my name. email. phone number and abn..

ive attched a file with my business logo. which i dont love the colours.. i was think a dark background with charcoal letters so something along those colour schumes but im open to ideas..

BRM Constructions

```html
<!DOCTYPE html>
<html lang="en">
<head>
<meta charset="utf-8">
<title>BRM Constructions – Business Card</title>
<link href="https://fonts.googleapis.com/css2?family=Open+Sans:wght@400;600;700&display=swap" rel="stylesheet">
<style>
  :root {
    --backdrop: #3b3430;
    --card: #0e0e0e;
    --silver: #b9b9b9;
    --silver-dim: #8d8d8d;
    --detail: #a6a6a6;
  }
  * { margin: 0; padding: 0; box-sizing: border-box; }
  html, body {
    width: 1200px;
    height: 900px;
    overflow: hidden;
    background: var(--backdrop);
    font-family: "Open Sans", Arial, sans-serif;
  }
  .stage {
    position: relative;
    width: 1200px;
    height: 900px;
  }
  .card {
    position: absolute;
    top: 305px;
    width: 500px;
    height: 290px;
    background: var(--card);
    border-radius: 3px;
    box-shadow: 0 10px 30px rgba(0,0,0,0.45);
  }
  .card--back { left: 80px; }
  .card--front { left: 620px; }

  .brand {
    display: flex;
    align-items: center;
    gap: 10px;
    color: var(--silver);
    font-weight: 700;
    letter-spacing: 1px;
    white-space: nowrap;
  }
  .brand__mark {
    width: 14px;
    height: 14px;
    background: var(--silver);
  }
  .card--front .brand {
    position: absolute;
    left: 50%;
    top: 50%;
    transform: translate(-50%, -50%);
    font-size: 30px;
  }
  .card--back .brand {
    position: absolute;
    left: 34px;
    top: 128px;
    font-size: 20px;
    color: var(--silver-dim);
  }
  .card--back .brand__mark { width: 11px; height: 11px; background: var(--silver-dim); }

  .details {
    position: absolute;
    left: 300px;
    top: 60px;
    color: var(--detail);
  }
  .details__name {
    font-size: 15px;
    font-weight: 600;
    color: var(--silver);
  }
  .details__role {
    font-size: 12px;
    margin-top: 1px;
  }
  .details__abn {
    font-size: 12px;
    font-weight: 600;
    margin-top: 18px;
  }
  .contact {
    list-style: none;
    margin-top: 20px;
  }
  .contact__item {
    display: flex;
    align-items: center;
    gap: 10px;
    font-size: 12px;
    line-height: 20px;
  }
  .contact__icon {
    width: 10px;
    height: 10px;
    fill: var(--detail);
  }
</style>
</head>
<body>
<main class="stage">
  <section class="card card--back" aria-label="Card back with contact details">
    <div class="brand">
      <span class="brand__mark"></span>
      <span class="brand__name">BRM Constructions</span>
    </div>
    <div class="details">
      <p class="details__name">Daniel Reeves</p>
      <p class="details__role">Managing Director</p>
      <p class="details__abn">ABN : 12345678</p>
      <ul class="contact">
        <li class="contact__item">
          <svg class="contact__icon" viewBox="0 0 10 10" aria-hidden="true"><path d="M2 0.5 L3.6 2.6 L2.8 3.6 C3.4 5 5 6.6 6.4 7.2 L7.4 6.4 L9.5 8 L8.4 9.5 C4.5 9.2 0.8 5.5 0.5 1.6 Z"/></svg>
          <span>044-987 654 321</span>
        </li>
        <li class="contact__item">
          <svg class="contact__icon" viewBox="0 0 10 10" aria-hidden="true"><path d="M0.5 2 H9.5 V8.5 H0.5 Z M1 2.5 L5 5.5 L9 2.5" stroke="#0e0e0e" stroke-width="0.8"/></svg>
          <span>info@brmbuild.com</span>
        </li>
        <li class="contact__item">
          <svg class="contact__icon" viewBox="0 0 10 10" aria-hidden="true"><circle cx="5" cy="5" r="4.5"/><path d="M0.5 5 H9.5 M5 0.5 C3 3 3 7 5 9.5 M5 0.5 C7 3 7 7 5 9.5" stroke="#0e0e0e" stroke-width="0.7" fill="none"/></svg>
          <span>www.brmbuild.com</span>
        </li>
      </ul>
    </div>
  </section>

  <section class="card card--front" aria-label="Card front with company name">
    <div class="brand">
      <span class="brand__mark"></span>
      <span class="brand__name">BRM Constructions</span>
    </div>
  </section>
</main>
</body>
</html>
```